Calder Vossik - Cinematographer

NEED:
I'm looking for a sleek, professional, modern business card that will give give the recipient the impression that they can trust their production will go smoothly by hiring me. I will bring creativity and knowledge to their shoot, so that we can create powerful images.
I am looking for a card with a strong style and design ethos that could be expanded to a website and a full visual/graphic/design entity for me.
ABOUT ME:
I am a mid-twenties cinematographer, I work on music video, narrative short, commercial, and corporate projects. I blend the science and artistry of cameras and filmmaking to tell a story. I'm an artist, a technician, and a manager.
DESIGN:
I like sleek, simple design. Black, dark grays, white, dark navy, steel blues, I love cyan, but also cyan and red. I am not a fan of earthy tones. I generally prefer modern, san-serif fonts over serifs. My old logo was based on an aperture, a multi-blade device at the back of a lens that controls how much light passes through, but I made it with so many colors, that it doesn't necessarily lend itself to a specific color-scheme or design ethos. I liked that the aperture design provided a sense of the technical requirements of my job. I'm a fan of matte business cards, but am open to plenty of specialty print processes to make an outstanding card.
ATTACHED FILES:
My Old Rainbox Aperture Logo, plus a few designs I've tried playing around with, but am not tied to. I AM OPEN TO NEW DESIGNS, DO NOT FEEL TIED TO THIS.
**I've pulled my old logo down from the attached files, and instead attached other business cards I like, so as not to mislead you where I would like to go.
INFO:
Name: Calder Vossik
Job: Cinematographer
Email: ccvossik@lumenpost.net
Phone: 415.555.0193
Website: caldervossik.com
Updates
I'm adding some images of other cards that I like, and removing my old logo, since I'm looking for something new, and don't want that old logo to push anyone a certain direction.

```html
<!DOCTYPE html>
<html lang="en">
<head>
<meta charset="utf-8">
<title>Calder Vossik – Cinematographer Business Card</title>
<link rel="stylesheet" href="https://fonts.googleapis.com/css2?family=Montserrat:wght@300;500;700&display=swap">
<style>
  :root {
    --page: #e9eaec;
    --card-black: #0d0d0f;
    --card-charcoal: #242428;
    --white: #ffffff;
    --soft-grey: #c9ccd2;
    --cyan: #1fa6e6;
    --cyan-deep: #0a74c9;
    --mark: #2cc2e8;
  }
  * { margin: 0; padding: 0; box-sizing: border-box; }
  html, body {
    width: 1200px; height: 913px; overflow: hidden;
    background: var(--page);
    font-family: "Montserrat", Arial, sans-serif;
  }
  .canvas {
    width: 1200px; height: 913px;
    display: flex; align-items: center; justify-content: center; gap: 40px;
  }
  .card {
    position: relative;
    width: 540px; height: 309px;
    border-radius: 4px;
    overflow: hidden;
    background: linear-gradient(135deg, var(--card-charcoal) 0%, var(--card-black) 60%);
    box-shadow: 0 10px 26px rgba(0,0,0,.22);
    color: var(--white);
  }
  .lockup {
    position: absolute;
    display: flex; align-items: center; gap: 14px;
    white-space: nowrap;
  }
  .lockup__dot {
    width: 30px; height: 30px; border-radius: 50%;
    background: var(--mark);
    flex: none;
  }
  .lockup__name {
    font-weight: 700; letter-spacing: .05em; text-transform: uppercase;
    color: var(--white); line-height: 1;
  }
  .lockup__role {
    font-weight: 300; letter-spacing: .32em; text-transform: uppercase;
    color: var(--soft-grey); margin-top: 8px;
  }
  .card--front .lockup { left: 50%; top: 50%; transform: translate(-50%, -50%); }
  .card--front .lockup__name { font-size: 32px; }
  .card--front .lockup__role { font-size: 14px; }

  .card--back .lockup { left: 30px; top: 190px; gap: 10px; }
  .card--back .lockup__dot { width: 20px; height: 20px; }
  .card--back .lockup__name { font-size: 19px; }
  .card--back .lockup__role { font-size: 9px; margin-top: 6px; letter-spacing: .28em; }

  .accent-panel {
    position: absolute; top: 0; right: 0; bottom: 0; width: 220px;
    background: linear-gradient(160deg, var(--cyan) 0%, var(--cyan-deep) 100%);
  }

  .identity {
    position: absolute; right: 24px; top: 30px; text-align: right;
  }
  .identity__name { font-size: 17px; font-weight: 700; }
  .identity__role { font-size: 10.5px; font-weight: 500; margin-top: 6px; color: var(--white); opacity: .85; }

  .contact {
    position: absolute; right: 22px; top: 150px;
    list-style: none; text-align: right;
    font-size: 12px; font-weight: 500; color: var(--white);
  }
  .contact li {
    display: flex; align-items: center; justify-content: flex-end; gap: 8px;
    margin-bottom: 11px; white-space: nowrap;
  }
  .contact svg { width: 13px; height: 13px; fill: none; stroke: var(--white); stroke-width: 1.6; flex: none; }
</style>
</head>
<body>
<main class="canvas">

  <section class="card card--front" aria-label="Card front">
    <div class="lockup">
      <span class="lockup__dot"></span>
      <div>
        <div class="lockup__name">Calder Vossik</div>
        <div class="lockup__role">Cinematographer</div>
      </div>
    </div>
  </section>

  <section class="card card--back" aria-label="Card back">
    <div class="accent-panel" role="img" aria-label="Decorative cyan and red wave graphic"></div>

    <div class="identity">
      <div class="identity__name">Calder Vossik</div>
      <div class="identity__role">Cinematographer</div>
    </div>

    <ul class="contact">
      <li>415.555.0193
        <svg viewBox="0 0 16 16"><path d="M4 2 L6.5 2 L7.5 5.5 L5.8 6.8 C6.6 8.6 7.6 9.6 9.4 10.4 L10.6 8.6 L14 9.6 L14 12.2 C14 13.2 13.2 14 12 14 C6.8 13.6 2.4 9.2 2 4 C2 2.8 2.8 2 4 2 Z"/></svg>
      </li>
      <li>ccvossik@lumenpost.net
        <svg viewBox="0 0 16 16"><rect x="1.5" y="3.5" width="13" height="9"/><path d="M1.5 3.5 L8 9 L14.5 3.5"/></svg>
      </li>
      <li>www.caldervossik.com
        <svg viewBox="0 0 16 16"><circle cx="8" cy="8" r="6.5"/><ellipse cx="8" cy="8" rx="2.8" ry="6.5"/><path d="M1.5 8 H14.5"/></svg>
      </li>
    </ul>

    <div class="lockup">
      <span class="lockup__dot"></span>
      <div>
        <div class="lockup__name">Calder Vossik</div>
        <div class="lockup__role">Cinematographer</div>
      </div>
    </div>
  </section>

</main>
</body>
</html>
```